Tech business card design

We need an amazing business card design for our new business 'Pexla' a marketing tech startup based in Sydney, Australia. We provide an online marketplace for businesses to search and buy advertising media, connect with service providers and learn more about marketing. We wish to communicate 'cool tech', reliability and professionalism and design based around our logo.

Target Market(s)

Business Owners

Contact Information for Business Card

Name
Position
Email Address
Website
Phone Number

Font styles to use
Other font styles liked:
• Avenir & Avenir Next

Colors

Designer to choose colors to be used in the design.

```html
<!DOCTYPE html>
<html lang="en">
<head>
<meta charset="utf-8">
<title>Pexla Business Card</title>
<link href="https://fonts.googleapis.com/css2?family=Source+Sans+3:wght@400;600;700;800&display=swap" rel="stylesheet">
<style>
  :root {
    --backdrop: #94a8b3;
    --card: #ffffff;
    --ink: #231f20;
    --navy: #11123a;
    --rule: #2b3a7a;
  }
  html, body {
    margin: 0;
    padding: 0;
    width: 1079px;
    height: 1200px;
    overflow: hidden;
    background: var(--backdrop);
    font-family: "Source Sans 3", sans-serif;
    color: var(--ink);
  }
  .canvas {
    position: relative;
    width: 1079px;
    height: 1200px;
  }
  .card {
    position: absolute;
    width: 904px;
    height: 517px;
    background: var(--card);
    border-radius: 26px;
  }
  .card--front { left: 87px; top: 51px; }
  .card--back { left: 80px; top: 630px; }

  .identity {
    position: absolute;
    right: 502px;
    top: 221px;
    text-align: right;
    white-space: nowrap;
  }
  .identity__name {
    margin: 0;
    font-size: 48px;
    font-weight: 700;
    line-height: 1;
    letter-spacing: -0.5px;
  }
  .identity__role {
    margin: 10px 0 0;
    font-size: 54px;
    font-weight: 400;
    line-height: 1;
  }
  .divider {
    position: absolute;
    left: 448px;
    top: 182px;
    width: 2px;
    height: 173px;
    background: var(--rule);
  }
  .contact {
    position: absolute;
    left: 495px;
    top: 179px;
    margin: 0;
    padding: 0;
    list-style: none;
    font-size: 26px;
    line-height: 1;
    white-space: nowrap;
  }
  .contact__item {
    display: flex;
    align-items: center;
    height: 38px;
  }
  .contact__icon {
    width: 22px;
    height: 22px;
    margin-right: 9px;
    flex: none;
  }
  .contact__web { letter-spacing: 2.5px; }
  .contact__address {
    margin-top: 0;
    font-size: 25px;
    line-height: 30px;
  }

  .wordmark {
    position: absolute;
    left: 0;
    right: 0;
    top: 128px;
    text-align: center;
    font-size: 220px;
    font-weight: 800;
    line-height: 1;
    color: var(--navy);
    letter-spacing: -4px;
  }
  .back-web {
    position: absolute;
    left: 0;
    right: 0;
    top: 426px;
    text-align: center;
    font-size: 30px;
    letter-spacing: 4px;
    color: #000;
  }
</style>
</head>
<body>
<main class="canvas">
  <section class="card card--front">
    <div class="identity">
      <h1 class="identity__name">JOHN SMITH</h1>
      <p class="identity__role">Position</p>
    </div>
    <div class="divider"></div>
    <ul class="contact">
      <li class="contact__item">
        <svg class="contact__icon" viewBox="0 0 24 24" aria-hidden="true">
          <circle cx="12" cy="12" r="10.5" fill="none" stroke="#231f20" stroke-width="1.6"/>
          <path d="M9 6.5 L11 9.5 L9.8 11 C10.5 12.6 11.6 13.8 13.1 14.6 L14.5 13.4 L17.5 15.4 L16.2 17.6 C12 17.6 7 12.6 7 8 Z" fill="#231f20"/>
        </svg>
        <span>012-345-6789</span>
      </li>
      <li class="contact__item">
        <svg class="contact__icon" viewBox="0 0 24 24" aria-hidden="true">
          <rect x="1" y="5" width="22" height="14" fill="#231f20"/>
          <path d="M2 6 L12 13 L22 6 M2 18 L9 11.5 M22 18 L15 11.5" fill="none" stroke="#fff" stroke-width="1.4"/>
        </svg>
        <span>info@pexla.com</span>
      </li>
      <li class="contact__item">
        <svg class="contact__icon" viewBox="0 0 24 24" aria-hidden="true">
          <g fill="none" stroke="#231f20" stroke-width="1.5">
            <circle cx="12" cy="12" r="10"/>
            <ellipse cx="12" cy="12" rx="4.5" ry="10"/>
            <path d="M2 12 H22 M3.5 7 H20.5 M3.5 17 H20.5 M12 2 V22"/>
          </g>
        </svg>
        <span class="contact__web">www.pexla.com</span>
      </li>
      <li class="contact__address">Street name City Name,<br>Zipcode,012345</li>
    </ul>
  </section>

  <section class="card card--back">
    <div class="wordmark">pexla</div>
    <div class="back-web">www.pexla.com</div>
  </section>
</main>
</body>
</html>
```